Communication and Marketing agency needs a new presentation card

We are a group of communication and marketing agencies specialized in companies that are in the logistics and industrial sector. The head agency is TELVANO Grupo and the group consists of 4 agencies: TELVANO Media, TELVANO Digital, TELVANO Research and DifundeEnPantalla. We hace 4 offices in Spain (Madrid, Barcelona, Valencia and Murcia). We are looking for a clean and attractive design that transmits our experience, brand presence in the market and knowledge to those who receive the card.It has to maintain the colors of the logo that is attached.
Target Market(s)
logistics and industrial sector
Marketing department
Contact Information for Business Card
Clean and attractive design

```html
<!DOCTYPE html>
<html lang="es">
<head>
<meta charset="utf-8">
<title>TELVANO Grupo – tarjetas</title>
<link href="https://fonts.googleapis.com/css2?family=Open+Sans:wght@400;700&display=swap" rel="stylesheet">
<style>
  :root {
    --page: #3a332f;
    --card: #1f2023;
    --red: #c1272d;
    --white: #f2f2f2;
    --silver: #b9b9bb;
    --rule: #9a9a9c;
  }
  * { box-sizing: border-box; margin: 0; padding: 0; }
  html, body { width: 1200px; height: 864px; overflow: hidden; }
  body {
    background: var(--page);
    font-family: "Open Sans", Arial, sans-serif;
    position: relative;
  }
  .card {
    position: absolute;
    width: 560px;
    height: 320px;
    background: var(--card);
    box-shadow: 0 14px 30px rgba(0,0,0,.45);
    color: var(--white);
  }
  /* Group side */
  .card--group { left: 60px; top: 90px; }
  .group-name {
    position: absolute;
    left: 0; right: 0; top: 92px;
    text-align: center;
    font-size: 44px;
    font-weight: 400;
    letter-spacing: 4px;
    color: var(--silver);
  }
  .agency-list {
    position: absolute;
    left: 24px; right: 24px; bottom: 38px;
    display: flex;
    justify-content: space-between;
    list-style: none;
  }
  .agency-list li {
    font-size: 14px;
    font-weight: 400;
    color: var(--white);
    letter-spacing: .5px;
    text-align: center;
  }
  /* Contact side */
  .card--contact { left: 580px; top: 450px; }
  .person-name {
    position: absolute; left: 34px; top: 34px;
    color: var(--red); font-weight: 700; font-size: 22px;
  }
  .person-role {
    position: absolute; left: 34px; top: 64px;
    font-size: 14px;
  }
  .divider {
    position: absolute; left: 180px; right: 22px; top: 102px;
    height: 1px; background: var(--rule);
  }
  .brand-mark {
    position: absolute; right: 30px; top: 36px;
    color: var(--red); font-size: 26px; font-weight: 400; letter-spacing: 2px;
  }
  .contact-list {
    position: absolute; left: 34px; top: 118px;
    list-style: none;
  }
  .contact-list li {
    display: flex; align-items: center; gap: 10px;
    font-size: 14px; line-height: 24px;
  }
  .contact-list svg { width: 13px; height: 13px; flex: none; }
  .office-list {
    position: absolute; right: 30px; bottom: 26px;
    list-style: none; text-align: right;
  }
  .office-list li { font-size: 15px; line-height: 21px; }
  .office-list li::after {
    content: ""; display: inline-block; width: 4px; height: 4px;
    border-radius: 50%; background: var(--red);
    margin-left: 7px; vertical-align: middle;
  }
</style>
</head>
<body>

<section class="card card--group" aria-label="Reverso de la tarjeta">
  <h1 class="group-name">TELVANO Grupo</h1>
  <ul class="agency-list">
    <li>TELVANO Digital</li>
    <li>TELVANO Media</li>
    <li>TELVANO Research</li>
    <li>DifundeEnPantalla</li>
  </ul>
</section>

<section class="card card--contact" aria-label="Anverso de la tarjeta">
  <h2 class="person-name">Lorenzo Ibarra</h2>
  <p class="person-role">Director</p>
  <div class="divider"></div>
  <p class="brand-mark">TELVANO Media</p>

  <ul class="contact-list">
    <li>
      <svg viewBox="0 0 16 16" aria-hidden="true"><path fill="#c1272d" d="M3 1h3l1 4-2 1a9 9 0 0 0 5 5l1-2 4 1v3a2 2 0 0 1-2 2A13 13 0 0 1 1 3a2 2 0 0 1 2-2z"/></svg>
      910 555 214
    </li>
    <li>
      <svg viewBox="0 0 16 16" aria-hidden="true"><rect x="4" y="1" width="8" height="14" rx="1.5" fill="none" stroke="#c1272d" stroke-width="1.8"/><circle cx="8" cy="12.5" r="1" fill="#c1272d"/></svg>
      600 555 781
    </li>
    <li>
      <svg viewBox="0 0 16 16" aria-hidden="true"><rect x="1" y="3" width="14" height="10" fill="#c1272d"/><path d="M1 3l7 6 7-6" fill="none" stroke="#1f2023" stroke-width="1.4"/></svg>
      libarra@telvano.es
    </li>
    <li>
      <svg viewBox="0 0 16 16" aria-hidden="true"><rect x="1" y="1" width="14" height="14" rx="2" fill="#c1272d"/></svg>
      lorenzoibarra
    </li>
    <li>
      <svg viewBox="0 0 16 16" aria-hidden="true"><circle cx="8" cy="8" r="7" fill="#c1272d"/><path d="M1 8h14M8 1c3 3 3 11 0 14M8 1c-3 3-3 11 0 14" fill="none" stroke="#1f2023" stroke-width="1"/></svg>
      telvano.es
    </li>
  </ul>

  <ul class="office-list">
    <li>Madrid</li>
    <li>Barcelona</li>
    <li>Valencia</li>
    <li>Murcia</li>
  </ul>
</section>

</body>
</html>
```